Business Card - connecting 2 souls and beggining the journey of self discovery

Logo on the front
with tag line

On the back list of services and contact details

Seminars
workshops
Coaching
podcasts

Darren Whitlow
Health & Wellbeing Life Coach
0491 372 615
darren@brightcoreliving.example
brightcoreliving.example

Industry/Entity Type

Life Coaching

Contact Information for Business Card

I like the use of colour from the logo to be used. I'm not a fan of white.

Requirements
Must have
• My tagline: The journey home starts with you
Nice to have
• Use of colour that is in the Brightcore Living logo

```html
<!DOCTYPE html>
<html lang="en">
<head>
<meta charset="utf-8">
<title>Brightcore Living – Business Card</title>
<link rel="stylesheet" href="https://fonts.googleapis.com/css2?family=Montserrat:wght@300;500;600;700&display=swap">
<style>
  :root {
    --teal: #1a9e91;
    --ink: #1d1d1f;
    --muted: #444448;
    --paper: #ffffff;
    --backdrop: #e4e5e7;
    --brand-dot: #f29a3a;
  }
  * { box-sizing: border-box; margin: 0; padding: 0; }
  html, body {
    width: 1200px; height: 861px; overflow: hidden;
    background: var(--backdrop);
    font-family: "Montserrat", Arial, sans-serif;
  }
  .canvas { position: relative; width: 1200px; height: 861px; }

  .card {
    position: absolute;
    width: 620px; height: 355px;
    border-radius: 26px;
    box-shadow: 0 10px 28px rgba(0,0,0,.14);
    overflow: hidden;
  }

  /* Front */
  .card--front {
    left: 80px; top: 50px;
    background: var(--teal);
    display: flex; flex-direction: column; align-items: center; justify-content: center;
    gap: 18px;
  }
  .brand { display: flex; align-items: center; gap: 12px; }
  .brand__dot {
    width: 34px; height: 34px; border-radius: 50%;
    background: var(--brand-dot);
  }
  .brand__name { font-weight: 700; letter-spacing: .5px; white-space: nowrap; }
  .card--front .brand__name { color: var(--paper); font-size: 30px; }
  .tagline { font-weight: 600; white-space: nowrap; }
  .card--front .tagline { color: var(--paper); font-size: 19px; }

  /* Back */
  .card--back {
    left: 500px; top: 456px;
    background: var(--paper);
  }
  .back__brand {
    position: absolute; left: 18px; top: 62px; width: 272px;
    display: flex; flex-direction: column; align-items: center; gap: 18px;
  }
  .card--back .brand { flex-direction: column; gap: 14px; }
  .card--back .brand__dot { width: 96px; height: 96px; }
  .card--back .brand__name { color: var(--ink); font-size: 22px; }
  .card--back .tagline { color: var(--ink); font-size: 13.5px; }

  .divider {
    position: absolute; left: 300px; top: 48px;
    width: 1.5px; height: 168px; background: var(--teal);
  }
  .contact { position: absolute; left: 328px; top: 50px; right: 20px; }
  .contact__name { font-size: 25px; font-weight: 700; color: var(--ink); line-height: 1.1; }
  .contact__name span { color: var(--teal); }
  .contact__role { font-size: 12.5px; font-weight: 300; color: var(--muted); margin-top: 3px; }
  .contact__list { list-style: none; margin-top: 22px; display: flex; flex-direction: column; gap: 14px; }
  .contact__item { display: flex; align-items: center; gap: 12px; font-size: 12px; font-weight: 500; color: var(--ink); white-space: nowrap; }
  .contact__icon {
    width: 26px; height: 26px; border-radius: 50%; background: var(--teal);
    display: flex; align-items: center; justify-content: center; flex: none;
  }

  .services {
    position: absolute; left: 40px; right: 30px; bottom: 36px;
    list-style: none; display: flex; justify-content: space-between;
  }
  .services li {
    color: var(--teal); font-weight: 600; font-size: 17px;
    display: flex; align-items: center; gap: 8px;
  }
  .services li::before {
    content: ""; width: 6px; height: 6px; border-radius: 50%; background: var(--teal);
  }
</style>
</head>
<body>
<main class="canvas">

  <section class="card card--front" aria-label="Card front">
    <div class="brand">
      <span class="brand__dot"></span>
      <span class="brand__name">Brightcore Living</span>
    </div>
    <p class="tagline">The journey home starts with you</p>
  </section>

  <section class="card card--back" aria-label="Card back">
    <div class="back__brand">
      <div class="brand">
        <span class="brand__dot"></span>
        <span class="brand__name">Brightcore Living</span>
      </div>
      <p class="tagline">The journey home starts with you</p>
    </div>

    <div class="divider"></div>

    <div class="contact">
      <h1 class="contact__name">Darren <span>Whitlow</span></h1>
      <p class="contact__role">Health &amp; Wellbeing Life Coach</p>
      <ul class="contact__list">
        <li class="contact__item">
          <span class="contact__icon">
            <svg width="14" height="14" viewBox="0 0 24 24" fill="#fff"><path d="M6.6 10.8a15.2 15.2 0 0 0 6.6 6.6l2.2-2.2a1 1 0 0 1 1-.25 11.4 11.4 0 0 0 3.6.57 1 1 0 0 1 1 1V20a1 1 0 0 1-1 1A17 17 0 0 1 3 4a1 1 0 0 1 1-1h3.5a1 1 0 0 1 1 1c0 1.25.2 2.45.57 3.57a1 1 0 0 1-.25 1z"/></svg>
          </span>
          0491 372 615
        </li>
        <li class="contact__item">
          <span class="contact__icon">
            <svg width="14" height="14" viewBox="0 0 24 24" fill="none" stroke="#fff" stroke-width="2"><rect x="3" y="5" width="18" height="14" rx="1"/><path d="M3 6l9 7 9-7"/></svg>
          </span>
          darren@brightcoreliving.example
        </li>
        <li class="contact__item">
          <span class="contact__icon">
            <svg width="14" height="14" viewBox="0 0 24 24" fill="none" stroke="#fff" stroke-width="2"><circle cx="12" cy="12" r="9"/><path d="M3 12h18M12 3c3 3 3 15 0 18M12 3c-3 3-3 15 0 18"/></svg>
          </span>
          www.brightcoreliving.example
        </li>
      </ul>
    </div>

    <ul class="services">
      <li>Seminars</li>
      <li>Coaching</li>
      <li>Workshops</li>
      <li>Podcasts</li>
    </ul>
  </section>

</main>
</body>
</html>
```